National Mission Critical Construction Contractor needs Stationery Design to make a bold statement

We are a small commercial construction company, working primarily in mission critical facilities across the U.S.. We have exciting corporate changes going an and a new logo and office space so we need new stationery. The final design should incorporate our new logo and invoke a fresh, high-tech feel while looking simple and modern.

Industry/Entity Type

Construction

Contact Information for Business Card

We are required to list our state licensing qualifications on the back of our card.

Font styles to use
Sans Serif

Requirements
Must have
• We need to have a design for second page of stationery, envelopes both standard and with a window and for a 3 x 4 notepad.

```html
<!DOCTYPE html>
<html lang="en">
<head>
<meta charset="utf-8">
<title>Northgate Construction – Business Card</title>
<link rel="stylesheet" href="https://fonts.googleapis.com/css2?family=Source+Sans+3:wght@400;600&display=swap">
<style>
  :root {
    --page-bg: #e9ebee;
    --frost-top: #eef2f5;
    --frost-bottom: #d6dfe7;
    --blue-left: #2a64b0;
    --blue-deep: #123f86;
    --ring-blue: #1d5aa6;
    --text-light: #ffffff;
    --text-soft: #dfe8f5;
    --text-muted: #c3d2e6;
    --brand-navy: #163f7a;
  }
  html, body {
    margin: 0;
    width: 1200px;
    height: 969px;
    overflow: hidden;
    background: var(--page-bg);
    font-family: "Source Sans 3", "Helvetica Neue", Arial, sans-serif;
  }
  .card {
    position: absolute;
    left: 188px;
    top: 248px;
    width: 872px;
    height: 494px;
    border-radius: 24px;
    overflow: hidden;
    box-shadow: 0 8px 26px rgba(20, 40, 70, 0.16);
  }
  .card-art {
    position: absolute;
    inset: 0;
  }
  .holder {
    position: absolute;
    left: 64px;
    top: 66px;
    color: var(--text-light);
  }
  .holder-name {
    margin: 0;
    font-size: 30px;
    font-weight: 600;
    letter-spacing: 0.5px;
    line-height: 36px;
  }
  .holder-title {
    margin: 0;
    font-size: 22px;
    line-height: 28px;
    color: var(--text-soft);
  }
  .address {
    position: absolute;
    left: 64px;
    top: 191px;
    margin: 0;
    font-style: normal;
    font-size: 22px;
    line-height: 33px;
    color: var(--text-light);
  }
  .contact-list {
    position: absolute;
    left: 64px;
    top: 276px;
    margin: 0;
    padding: 0;
    list-style: none;
    font-size: 22px;
    color: var(--text-light);
  }
  .contact-list li {
    display: flex;
    align-items: center;
    height: 33px;
    white-space: nowrap;
  }
  .contact-list li.muted { color: var(--text-muted); }
  .contact-icon {
    width: 19px;
    height: 19px;
    margin-right: 14px;
    fill: var(--text-soft);
  }
  .brand {
    position: absolute;
    left: 408px;
    top: 280px;
    width: 480px;
    display: flex;
    align-items: center;
    justify-content: center;
    gap: 12px;
    white-space: nowrap;
  }
  .brand-dot {
    width: 22px;
    height: 22px;
    border-radius: 50%;
    background: var(--brand-navy);
    flex: none;
  }
  .brand-name {
    font-size: 30px;
    font-weight: 600;
    letter-spacing: 1px;
    color: var(--brand-navy);
  }
</style>
</head>
<body>
  <div class="card">
    <svg class="card-art" viewBox="0 0 872 494" width="872" height="494" aria-hidden="true">
      <defs>
        <linearGradient id="frost" x1="0" y1="0" x2="0.3" y2="1">
          <stop offset="0" stop-color="var(--frost-top)"/>
          <stop offset="1" stop-color="var(--frost-bottom)"/>
        </linearGradient>
        <linearGradient id="blueBand" x1="0" y1="0" x2="1" y2="0">
          <stop offset="0" stop-color="var(--blue-left)"/>
          <stop offset="0.45" stop-color="var(--blue-deep)"/>
          <stop offset="0.7" stop-color="var(--blue-deep)" stop-opacity="0.55"/>
          <stop offset="0.85" stop-color="var(--blue-deep)" stop-opacity="0"/>
        </linearGradient>
        <mask id="outsideRing">
          <rect width="872" height="494" fill="#fff"/>
          <circle cx="660" cy="247" r="270" fill="#000"/>
        </mask>
      </defs>
      <rect width="872" height="494" fill="url(#frost)"/>
      <rect width="872" height="494" fill="url(#blueBand)" mask="url(#outsideRing)"/>
      <circle cx="660" cy="247" r="270" fill="none" stroke="var(--ring-blue)" stroke-width="6" opacity="0.85"/>
      <circle cx="660" cy="247" r="262" fill="none" stroke="#ffffff" stroke-width="2" opacity="0.45"/>
    </svg>

    <div class="holder">
      <p class="holder-name">DANIEL REYES</p>
      <p class="holder-title">CEO/Founder</p>
    </div>

    <address class="address">
      2140 Birchwood Court<br>
      Anchorage, Alaska 99507
    </address>

    <ul class="contact-list">
      <li>
        <svg class="contact-icon" viewBox="0 0 24 24"><path d="M6.6 10.8a15.1 15.1 0 0 0 6.6 6.6l2.2-2.2c.3-.3.7-.4 1-.2 1.1.4 2.3.6 3.6.6.6 0 1 .4 1 1V20c0 .6-.4 1-1 1A17 17 0 0 1 3 4c0-.6.4-1 1-1h3.5c.6 0 1 .4 1 1 0 1.3.2 2.5.6 3.6.1.3 0 .7-.2 1z"/></svg>
        907 555 0142
      </li>
      <li>
        <svg class="contact-icon" viewBox="0 0 24 24"><path d="M7 1h10a2 2 0 0 1 2 2v18a2 2 0 0 1-2 2H7a2 2 0 0 1-2-2V3a2 2 0 0 1 2-2zm0 3v14h10V4zm5 15.5a1.2 1.2 0 1 0 0 2.4 1.2 1.2 0 0 0 0-2.4z"/></svg>
        907 555 0187
      </li>
      <li>
        <svg class="contact-icon" viewBox="0 0 24 24"><path d="M6 2h10l2 2v5H6zm-2 8h16a2 2 0 0 1 2 2v6h-4v4H6v-4H2v-6a2 2 0 0 1 2-2zm4 7v3h8v-3z"/></svg>
        907 555 0163
      </li>
      <li>
        <svg class="contact-icon" viewBox="0 0 24 24"><path d="M2 5h20v14H2zm2 2v.5l8 5 8-5V7zm0 2.8V17h16V9.8l-8 5z"/></svg>
        daniel@northgatecm.com
      </li>
      <li class="muted">
        <svg class="contact-icon" viewBox="0 0 24 24"><path d="M12 2a10 10 0 1 0 0 20 10 10 0 0 0 0-20zm6.9 6h-3a15 15 0 0 0-1.3-3.9A8 8 0 0 1 18.9 8zM12 4c.8 1.1 1.5 2.5 1.9 4h-3.8c.4-1.5 1.1-2.9 1.9-4zM4.3 14a8 8 0 0 1 0-4h3.4a16 16 0 0 0 0 4zm.8 2h3a15 15 0 0 0 1.3 3.9A8 8 0 0 1 5.1 16zm3-8h-3a8 8 0 0 1 4.3-3.9C8.8 5.3 8.4 6.6 8.1 8zM12 20c-.8-1.1-1.5-2.5-1.9-4h3.8c-.4 1.5-1.1 2.9-1.9 4zm2.3-6H9.7a14 14 0 0 1 0-4h4.6a14 14 0 0 1 0 4zm.3 5.9c.6-1.2 1-2.5 1.3-3.9h3a8 8 0 0 1-4.3 3.9zm1.7-5.9a16 16 0 0 0 0-4h3.4a8 8 0 0 1 0 4z"/></svg>
        www.northgatecm.com
      </li>
    </ul>

    <div class="brand">
      <span class="brand-dot"></span>
      <span class="brand-name">NORTHGATE CONSTRUCTION</span>
    </div>
  </div>
</body>
</html>
```